Velvet Pressings Techno Label Business Card

I'm looking for a very clean business card for my Velvet Pressings music label. The label focusses on techno music. The card should include:

• my name : Tomas Brandt as "Founder & CEO"
• email address: tomas@velvet-pressings.example
• web: www.velvet-pressings.example
• facebook logo + /velvetpress
• twitter logo + /velvetpress
• soundcloud logo + /velvetpressings

Feel free to include your ideas! I'm looking forward to discuss about it.

Tomas

Industry/Entity Type

Business

Contact Information for Business Card

I don't like glossy cards. Prefer matt.

Requirements
Nice to have
• Maybe on one side the complete logo, other side just the icon.
Should not have
• Flashy stuff. Must be clean and business like style.

```html
<!DOCTYPE html>
<html lang="en">
<head>
<meta charset="utf-8">
<title>Velvet Pressings – Business Card</title>
<link rel="stylesheet" href="https://fonts.googleapis.com/css2?family=Jost:wght@400;500&display=swap">
<style>
  :root {
    --backdrop: #ecebe8;
    --card-white: #ffffff;
    --card-mist: #e4e4e4;
    --band-grey: #8c8c8c;
    --band-grey-dark: #7a7a7a;
    --accent-orange: #f26a10;
    --ink-grey: #7d7d7d;
    --text-light: #ffffff;
  }
  html, body {
    margin: 0;
    width: 1200px;
    height: 899px;
    overflow: hidden;
    background: var(--backdrop);
    font-family: "Jost", sans-serif;
  }
  .business-card {
    position: absolute;
    left: 180px;
    top: 210px;
    width: 840px;
    height: 480px;
    border-radius: 44px;
    overflow: hidden;
    box-shadow: 0 10px 30px rgba(0,0,0,0.12);
  }
  .card-surface {
    position: absolute;
    inset: 0;
    width: 100%;
    height: 100%;
  }
  .brand-lockup {
    position: absolute;
    left: 0;
    right: 0;
    top: 70px;
    display: flex;
    align-items: center;
    justify-content: center;
    gap: 16px;
    padding-right: 120px;
  }
  .brand-dot {
    width: 40px;
    height: 40px;
    border-radius: 50%;
    background: var(--accent-orange);
  }
  .brand-name {
    font-size: 50px;
    font-weight: 500;
    color: var(--ink-grey);
    letter-spacing: -0.5px;
  }
  .identity-block {
    position: absolute;
    right: 460px;
    top: 300px;
    text-align: right;
    color: var(--text-light);
    font-variant: small-caps;
    letter-spacing: 1.5px;
    line-height: 1.35;
  }
  .person-name {
    color: var(--accent-orange);
    font-size: 20px;
    font-weight: 500;
  }
  .person-role { font-size: 17px; margin-bottom: 12px; }
  .postal-address { font-size: 17px; font-style: normal; }
  .column-divider {
    position: absolute;
    left: 394px;
    top: 292px;
    width: 2px;
    height: 168px;
    background: var(--text-light);
  }
  .contact-list {
    position: absolute;
    left: 410px;
    top: 290px;
    margin: 0;
    padding: 0;
    list-style: none;
    color: var(--text-light);
    font-size: 16px;
    font-variant: small-caps;
    letter-spacing: 1.3px;
  }
  .contact-list li {
    display: flex;
    align-items: center;
    gap: 10px;
    height: 21px;
  }
  .contact-icon { width: 15px; height: 15px; flex: none; }
  .social-square {
    width: 15px;
    height: 15px;
    flex: none;
    border-radius: 3px;
    background: var(--accent-orange);
  }
</style>
</head>
<body>
  <article class="business-card">
    <svg class="card-surface" viewBox="0 0 840 480" aria-hidden="true">
      <defs>
        <linearGradient id="upper-sheen" x1="0" y1="0" x2="0" y2="1">
          <stop offset="0" stop-color="var(--card-white)"/>
          <stop offset="1" stop-color="var(--card-mist)"/>
        </linearGradient>
        <linearGradient id="lower-band" x1="0" y1="0" x2="0" y2="1">
          <stop offset="0" stop-color="var(--band-grey)"/>
          <stop offset="1" stop-color="var(--band-grey-dark)"/>
        </linearGradient>
      </defs>
      <rect width="840" height="480" fill="url(#upper-sheen)"/>
      <path d="M0,252 C250,196 520,330 840,292 L840,480 L0,480 Z" fill="url(#lower-band)"/>
      <path d="M0,238 C250,180 520,318 840,276" fill="none" stroke="var(--accent-orange)" stroke-width="5"/>
      <path d="M0,246 C250,190 520,326 840,286" fill="none" stroke="var(--card-white)" stroke-width="4"/>
    </svg>

    <div class="brand-lockup">
      <span class="brand-dot"></span>
      <span class="brand-name">Velvet Pressings</span>
    </div>

    <div class="identity-block">
      <div class="person-name">Tomas Brandt</div>
      <div class="person-role">Founder &amp; CEO</div>
      <address class="postal-address">Suite # 118, Dock Bldg,<br>NY 10452</address>
    </div>

    <div class="column-divider"></div>

    <ul class="contact-list">
      <li>
        <svg class="contact-icon" viewBox="0 0 18 18" aria-hidden="true"><rect width="18" height="18" rx="3" fill="var(--accent-orange)"/><path d="M5 4 L7.5 4 L8.5 7 L7 8 C7.8 9.8 8.4 10.4 10 11 L11 9.5 L14 10.5 L14 13 C9 13.5 4.5 9 5 4 Z" fill="var(--text-light)"/></svg>
        555-014-2290
      </li>
      <li>
        <svg class="contact-icon" viewBox="0 0 18 18" aria-hidden="true"><rect width="18" height="18" rx="3" fill="var(--accent-orange)"/><rect x="6" y="3" width="6" height="12" rx="1.2" fill="var(--text-light)"/></svg>
        555-018-6731
      </li>
      <li>
        <svg class="contact-icon" viewBox="0 0 18 18" aria-hidden="true"><rect width="18" height="18" rx="3" fill="var(--accent-orange)"/><rect x="4" y="7" width="10" height="7" fill="var(--text-light)"/><rect x="6" y="3.5" width="6" height="3" fill="var(--text-light)"/></svg>
        555-012-4408
      </li>
      <li>
        <svg class="contact-icon" viewBox="0 0 18 18" aria-hidden="true"><rect width="18" height="18" rx="3" fill="var(--accent-orange)"/><rect x="3.5" y="5" width="11" height="8" fill="var(--text-light)"/><path d="M3.5 5 L9 9.5 L14.5 5" fill="none" stroke="var(--accent-orange)" stroke-width="1.2"/></svg>
        tomas@velvet-pressings.example
      </li>
      <li>
        <svg class="contact-icon" viewBox="0 0 18 18" aria-hidden="true"><rect width="18" height="18" rx="3" fill="var(--accent-orange)"/><circle cx="9" cy="9" r="5" fill="none" stroke="var(--text-light)" stroke-width="1.4"/><path d="M4 9 H14 M9 4 C6.5 7 6.5 11 9 14 C11.5 11 11.5 7 9 4" fill="none" stroke="var(--text-light)" stroke-width="1"/></svg>
        www.velvet-pressings.example
      </li>
      <li>
        <span class="social-square" role="img" aria-label="Social profile marker"></span>
        /velvetpress
      </li>
      <li>
        <span class="social-square" role="img" aria-label="Social profile marker"></span>
        /velvetpress
      </li>
      <li>
        <span class="social-square" role="img" aria-label="Audio profile marker"></span>
        /velvetpressings
      </li>
    </ul>
  </article>
</body>
</html>
```